Contemporary Business card for Event Manager

Needed for my startup events company in Melbourne. Events I manage will be based within the fashion industry, sporting events, product launches etc. Not weddings or small dinner parties. Therfore I am after something professional and aimed at high end corporate market; but with the added emphasis on not being too conservative or boring. I am happy with a pop of colour e.g. yellow or copper foil.

Target Market(s)

fashion industry, design industry, high end sporting events e.g. Polo, Grand Prix, corporate clients,

Industry/Entity Type

Fashion

Contact Information for Business Card

side 1
Lucy Brandt (can be upper or lower case, have a feature full stop between first and surname, or at the end of the nameetc) I am open to ideas. I would also be fine with my initials or name as a logo on the front (if this is the case my full name would need to go on the second side of the card.
2nd side:
Mobile: +61 400 817 263
email: lucy.brandt@mailnest.com.au

on one side of the card:
event management | brand activation | Advisory Services

Font styles to use
Serif
Sans Serif

Requirements
Must have
• side 2 must have
• mobile number
• email address
• event management | brand activation | Advisory Services
• ** my full name (Lucy Brandt) must be on the card somewhere)
Nice to have
• 1st side
• I see the card stock being either a dark grey, light grey, natural white or black (all matt colours on unprocessed card). I see the writing being copper foil, or foil white or foil black.
• To give you a feel for me, think: contemporary, minimalist, I love line drawings, concrete, white with grey vein marble, copper, white, grey, black...yes I do like colour....yellow (but pops of colour) ;) I would like the card to look designer but 'on trend' as I deal with a lot of design and fashion clients....styles - think the sophistication and simplicity of Vireaux or urban contemporary.
• some examples of what I like. Although please don't leet this limit you...I really am happy to have something a little more urban or design focused like a line drawing of an object, person too or a photo image too.
• https://www.moodtackle.com/pin/830165427719302846/
• https://www.moodtackle.com/pin/607281935540173268/
• https://www.moodtackle.com/pin/318746205913457092/
• https://www.moodtackle.com/pin/41983627530918476/
• https://www.moodtackle.com/pin/53128940672419087/
• https://www.moodtackle.com/pin/90316284750638152/
• https://www.moodtackle.com/pin/734092618450362918/
• https://www.moodtackle.com/pin/926354081736215407/
• https://www.moodtackle.com/pin/481627093518704356/
Should not have
• should not look commercial or have cartoonish looking logos. However happy with a simple line drawing or logo with initials etc.

```html
<!DOCTYPE html>
<html lang="en">
<head>
<meta charset="utf-8">
<title>Lucy Brandt – Business Card</title>
<link href="https://fonts.googleapis.com/css2?family=Questrial&display=swap" rel="stylesheet">
<style>
  :root {
    --ink: #0c0c0c;
    --paper: #f4f4f5;
    --paper-white: #ffffff;
    --accent: #3a7cc0;
    --accent-line: #4a84c4;
    --stage: #d9d6d1;
  }
  * { box-sizing: border-box; margin: 0; padding: 0; }
  html, body { width: 1200px; height: 892px; overflow: hidden; }
  body {
    background: var(--stage);
    font-family: "Questrial", "Century Gothic", sans-serif;
    color: var(--ink);
    position: relative;
  }
  .card {
    position: absolute;
    left: 250px;
    width: 700px;
    height: 400px;
    overflow: hidden;
    box-shadow: 0 6px 18px rgba(0,0,0,.18);
  }
  .card--front { top: 26px; background: var(--paper); }
  .card--back  { top: 466px; background: var(--paper-white); }

  .band { position: absolute; background: var(--ink); }
  .band--left { left: 0; top: 0; bottom: 0; width: 92px; border-right: 10px solid var(--paper); }
  .card--back .band--left { border-right-color: var(--paper-white); }
  .band--left::after {
    content: ""; position: absolute; right: -13px; top: 0; bottom: 0; width: 3px; background: var(--accent-line);
  }
  .band--right {
    right: 0; top: 180px; bottom: 0; width: 92px; border-left: 10px solid var(--paper-white);
  }
  .band--right::before {
    content: ""; position: absolute; left: -13px; top: 0; bottom: 0; width: 3px; background: var(--accent-line);
  }

  /* front */
  .name {
    position: absolute; left: 140px; top: 96px;
    font-size: 44px; line-height: 1; letter-spacing: 1px;
  }

  /* back */
  .contact {
    position: absolute; left: 92px; right: 92px; top: 130px; text-align: center;
    font-size: 26px; line-height: 1.25;
  }
  .services {
    position: absolute; left: 52px; top: 262px; width: 580px; height: 112px;
    background: var(--accent); border: 4px solid var(--paper-white);
    border-radius: 28px; box-shadow: 0 0 0 2px var(--ink);
    color: var(--paper-white); font-size: 21px;
  }
  .service { position: absolute; white-space: nowrap; }
  .service--event { left: 36px; top: 12px; }
  .service--advisory { left: 170px; top: 62px; }
  .service--brand { right: 30px; top: 36px; }
</style>
</head>
<body>
  <section class="card card--front" aria-label="Card front">
    <div class="band band--left"></div>
    <p class="name">Lucy Brandt</p>
  </section>

  <section class="card card--back" aria-label="Card back">
    <div class="band band--left"></div>
    <div class="band band--right"></div>
    <div class="contact">
      <p class="contact__phone">+61 400 817 263</p>
      <p class="contact__email">lucy.brandt@mailnest.com.au</p>
    </div>
    <div class="services">
      <span class="service service--event">event management</span>
      <span class="service service--advisory">Advisory Services</span>
      <span class="service service--brand">brand activation</span>
    </div>
  </section>
</body>
</html>
```